Harbor Crestline (Business Card Design)

Need business cards designed. Something modern, chic, and sleek. Mabye the back of the card should be the navy blue that is in the logo and then just the logo on the back.

Target Market(s)

Those in the hotel, office, and renovation industry

Contact Information for Business Card

1. Logo 2. Dorian Fenwick 3. CEO/Founder 4. Phone: (833) HarbCre / (833) 427-2731 5. Email: dorian@theharborcrestline.com 6. Website: www.theharborcrestline.com

Font styles to use
Other font styles liked:
• Look at the logo font and base the font for everything else off of that.

Colors
0054AA
0677BA
7BADD7
CADEEF
E8F1F8

Requirements
Must have
• Colors that are associated in the logo
Nice to have
• Sleek modern clean and chic design.

```html
<!DOCTYPE html>
<html lang="en">
<head>
<meta charset="utf-8">
<title>Harbor Crestline — Business Card</title>
<link href="https://fonts.googleapis.com/css2?family=Montserrat:wght@400;500;600&display=swap" rel="stylesheet">
<style>
  :root {
    --navy: #131b45;
    --gold: #caa44b;
    --faint: #ebebeb;
    --divider: #ececec;
    --stage-dark: #303030;
    --stage-light: #ffffff;
    --card: #ffffff;
    --text: #2a2f45;
  }
  * { margin: 0; padding: 0; box-sizing: border-box; }
  html, body { width: 1200px; height: 2887px; overflow: hidden; }
  body {
    position: relative;
    background: var(--stage-light);
    font-family: "Montserrat", sans-serif;
  }
  .stage-dark {
    position: absolute; left: 0; top: 0;
    width: 1200px; height: 1440px;
    background: var(--stage-dark);
  }
  .card {
    position: absolute;
    width: 909px; height: 519px;
    background: var(--card);
    overflow: hidden;
    transform-origin: top left;
  }
  .card.on-dark { box-shadow: 0 26px 22px -14px rgba(0,0,0,.85); }
  .card.on-light { transform: scale(1.054); box-shadow: 0 6px 22px rgba(0,0,0,.22); }

  .card-back-1 { left: 145px; top: 109px; }
  .card-front-1 { left: 145px; top: 762px; }
  .card-back-2 { left: 121px; top: 1535px; }
  .card-front-2 { left: 121px; top: 2160px; }

  .decor { position: absolute; left: 0; top: 0; }

  .brand {
    position: absolute; left: 236px; top: 110px;
    transform: translateX(-50%);
    display: flex; flex-direction: column; align-items: center;
  }
  .brand-mark {
    width: 44px; height: 44px;
    background: var(--navy);
    margin-bottom: 34px;
  }
  .brand-name {
    color: var(--navy);
    font-weight: 600;
    font-size: 40px;
    line-height: 1.12;
    letter-spacing: 3px;
    text-align: center;
    text-transform: uppercase;
    white-space: nowrap;
  }

  .divider {
    position: absolute; left: 432px; top: 90px;
    width: 2px; height: 353px;
    background: var(--divider);
  }
  .person {
    position: absolute; left: 480px; top: 122px;
  }
  .person-name {
    color: var(--navy);
    font-weight: 600;
    font-size: 42px;
    line-height: 1;
    letter-spacing: .3px;
  }
  .person-role {
    color: var(--gold);
    font-weight: 500;
    font-size: 23px;
    margin-top: 16px;
  }
  .contact-list {
    position: absolute; left: 479px; top: 254px;
    list-style: none;
  }
  .contact-list li {
    display: flex; align-items: center;
    height: 28px; margin-bottom: 23px;
    color: var(--text);
    font-size: 20px;
    white-space: nowrap;
  }
  .contact-list svg { width: 25px; height: 25px; margin-right: 11px; flex: none; }

  .bar-navy {
    position: absolute; left: 0; bottom: 0;
    width: 446px; height: 18px;
    background: var(--navy);
    clip-path: polygon(0 0, 432px 0, 446px 100%, 0 100%);
  }
  .bar-gold {
    position: absolute; left: 444px; bottom: 0;
    width: 465px; height: 8px;
    background: var(--gold);
  }
</style>
</head>
<body>
  <div class="stage-dark"></div>

  <!-- Card back, dark stage -->
  <section class="card on-dark card-back-1">
    <svg class="decor" width="909" height="519" aria-hidden="true">
      <rect x="511" y="91" width="340" height="340" fill="none" stroke="var(--faint)" stroke-width="46" transform="rotate(45 681 261)"/>
    </svg>
    <div class="brand">
      <div class="brand-mark"></div>
      <div class="brand-name">Harbor<br>Crestline</div>
    </div>
  </section>

  <!-- Card front, dark stage -->
  <section class="card on-dark card-front-1">
    <svg class="decor" width="909" height="519" aria-hidden="true">
      <rect x="700" y="-120" width="330" height="330" fill="none" stroke="var(--faint)" stroke-width="44" transform="rotate(45 865 45)"/>
    </svg>
    <div class="brand">
      <div class="brand-mark"></div>
      <div class="brand-name">Harbor<br>Crestline</div>
    </div>
    <div class="divider"></div>
    <div class="person">
      <h1 class="person-name">Dorian Fenwick</h1>
      <p class="person-role">CEO/Founder</p>
    </div>
    <ul class="contact-list">
      <li><svg viewBox="0 0 24 24"><circle cx="12" cy="12" r="10.5" fill="none" stroke="var(--gold)" stroke-width="1.4"/><path d="M8.5 7.5l2 2-1 1.3c.7 1.4 1.8 2.5 3.2 3.2l1.3-1 2 2-1.2 1.5c-3.6-.4-7.2-4-7.6-7.6z" fill="none" stroke="var(--navy)" stroke-width="1.2" stroke-linejoin="round"/></svg>(833) HarbCre / (833) 427-2731</li>
      <li><svg viewBox="0 0 24 24"><circle cx="12" cy="12" r="10.5" fill="none" stroke="var(--gold)" stroke-width="1.4"/><rect x="7" y="8.5" width="10" height="7" fill="none" stroke="var(--navy)" stroke-width="1.2"/><path d="M7 8.5l5 4 5-4" fill="none" stroke="var(--navy)" stroke-width="1.2"/></svg>dorian@theharborcrestline.com</li>
      <li><svg viewBox="0 0 24 24"><circle cx="12" cy="12" r="10.5" fill="none" stroke="var(--gold)" stroke-width="1.4"/><circle cx="12" cy="12" r="5.5" fill="none" stroke="var(--navy)" stroke-width="1.2"/><ellipse cx="12" cy="12" rx="2.3" ry="5.5" fill="none" stroke="var(--navy)" stroke-width="1"/><path d="M6.5 12h11" stroke="var(--navy)" stroke-width="1"/></svg>www.theharborcrestline.com</li>
    </ul>
    <div class="bar-navy"></div>
    <div class="bar-gold"></div>
  </section>

  <!-- Card back, light stage -->
  <section class="card on-light card-back-2">
    <svg class="decor" width="909" height="519" aria-hidden="true">
      <rect x="511" y="91" width="340" height="340" fill="none" stroke="var(--faint)" stroke-width="46" transform="rotate(45 681 261)"/>
    </svg>
    <div class="brand">
      <div class="brand-mark"></div>
      <div class="brand-name">Harbor<br>Crestline</div>
    </div>
  </section>

  <!-- Card front, light stage -->
  <section class="card on-light card-front-2">
    <svg class="decor" width="909" height="519" aria-hidden="true">
      <rect x="700" y="-120" width="330" height="330" fill="none" stroke="var(--faint)" stroke-width="44" transform="rotate(45 865 45)"/>
    </svg>
    <div class="brand">
      <div class="brand-mark"></div>
      <div class="brand-name">Harbor<br>Crestline</div>
    </div>
    <div class="divider"></div>
    <div class="person">
      <h2 class="person-name">Dorian Fenwick</h2>
      <p class="person-role">CEO/Founder</p>
    </div>
    <ul class="contact-list">
      <li><svg viewBox="0 0 24 24"><circle cx="12" cy="12" r="10.5" fill="none" stroke="var(--gold)" stroke-width="1.4"/><path d="M8.5 7.5l2 2-1 1.3c.7 1.4 1.8 2.5 3.2 3.2l1.3-1 2 2-1.2 1.5c-3.6-.4-7.2-4-7.6-7.6z" fill="none" stroke="var(--navy)" stroke-width="1.2" stroke-linejoin="round"/></svg>(833) HarbCre / (833) 427-2731</li>
      <li><svg viewBox="0 0 24 24"><circle cx="12" cy="12" r="10.5" fill="none" stroke="var(--gold)" stroke-width="1.4"/><rect x="7" y="8.5" width="10" height="7" fill="none" stroke="var(--navy)" stroke-width="1.2"/><path d="M7 8.5l5 4 5-4" fill="none" stroke="var(--navy)" stroke-width="1.2"/></svg>dorian@theharborcrestline.com</li>
      <li><svg viewBox="0 0 24 24"><circle cx="12" cy="12" r="10.5" fill="none" stroke="var(--gold)" stroke-width="1.4"/><circle cx="12" cy="12" r="5.5" fill="none" stroke="var(--navy)" stroke-width="1.2"/><ellipse cx="12" cy="12" rx="2.3" ry="5.5" fill="none" stroke="var(--navy)" stroke-width="1"/><path d="M6.5 12h11" stroke="var(--navy)" stroke-width="1"/></svg>www.theharborcrestline.com</li>
    </ul>
    <div class="bar-navy"></div>
    <div class="bar-gold"></div>
  </section>
</body>
</html>
```